Veldmark Supplies Business Card

Professional business card that stand out to our potential customers. Front and back with clean modern design

Industry/Entity Type

Oil and gas

Contact Information for Business Card

Name, address, website , office phone and cell number

Requirements
Must have
• Editable files for each employee

```html
<!DOCTYPE html>
<html lang="en">
<head>
<meta charset="utf-8">
<title>Veldmark Supplies Business Card</title>
<link rel="stylesheet" href="https://fonts.googleapis.com/css2?family=Roboto:wght@400;500;700&display=swap">
<style>
  :root {
    --backdrop: #2b2b2d;
    --brand-red: #dc1c24;
    --brand-blue: #22a7d3;
    --gradient-red: #d52432;
    --gradient-mid: #7a5a78;
    --paper: #f6f6f6;
    --ink: #333333;
    --white: #ffffff;
  }
  * { box-sizing: border-box; margin: 0; padding: 0; }
  html, body {
    width: 1200px; height: 852px; overflow: hidden;
    background: var(--backdrop);
    font-family: "Roboto", Arial, sans-serif;
  }
  .canvas {
    position: relative; width: 1200px; height: 852px;
  }
  .card {
    position: absolute; top: 278px;
    width: 520px; height: 296px;
    border-radius: 26px; overflow: hidden;
    box-shadow: 0 14px 30px rgba(0,0,0,.45);
  }
  .card--front {
    left: 50px;
    background: linear-gradient(200deg, var(--gradient-red) 0%, var(--gradient-mid) 48%, var(--brand-blue) 100%);
    display: flex; align-items: center; justify-content: center;
  }
  .front-brand {
    display: flex; flex-direction: column; align-items: center; gap: 14px;
  }
  .brand-square {
    width: 58px; height: 58px; border: 5px solid var(--white);
  }
  .brand-name {
    color: var(--white); font-weight: 700; font-size: 26px;
    letter-spacing: 2px; text-transform: uppercase;
  }
  .card--back {
    left: 630px; background: var(--paper);
  }
  .back-shape { position: absolute; inset: 0; }
  .back-brand {
    position: absolute; left: 30px; top: 0; width: 200px; height: 296px;
    display: flex; flex-direction: column; align-items: center; justify-content: center; gap: 12px;
  }
  .back-brand .brand-name { font-size: 20px; letter-spacing: 1.5px; text-align: center; line-height: 1.25; }
  .contact {
    position: absolute; left: 306px; top: 62px; color: var(--ink);
  }
  .contact__name { color: var(--brand-blue); font-weight: 500; font-size: 18px; }
  .contact__title { font-size: 12px; margin-top: 3px; }
  .contact__address { font-size: 12px; margin-top: 18px; line-height: 1.35; }
  .contact__list { list-style: none; margin-top: 10px; font-size: 12px; }
  .contact__list li { display: flex; align-items: center; gap: 7px; line-height: 1.45; }
  .contact__list svg { width: 11px; height: 11px; fill: var(--brand-red); flex: none; }
</style>
</head>
<body>
<main class="canvas">
  <section class="card card--front" aria-label="Card front">
    <div class="front-brand">
      <span class="brand-square"></span>
      <span class="brand-name">Veldmark Supplies</span>
    </div>
  </section>

  <section class="card card--back" aria-label="Card back">
    <svg class="back-shape" viewBox="0 0 520 296" preserveAspectRatio="none" aria-hidden="true">
      <ellipse cx="80" cy="250" rx="212" ry="230" fill="var(--brand-blue)"/>
      <ellipse cx="66" cy="254" rx="212" ry="232" fill="var(--brand-red)"/>
    </svg>
    <div class="back-brand">
      <span class="brand-square"></span>
      <span class="brand-name">Veldmark<br>Supplies</span>
    </div>
    <div class="contact">
      <p class="contact__name">Dana Rhee Calloway</p>
      <p class="contact__title">Managing Director</p>
      <p class="contact__address">412 Mesa Ridge Suite 7<br>Midland, Tx 79701</p>
      <ul class="contact__list">
        <li><svg viewBox="0 0 24 24"><path d="M6.6 10.8a15 15 0 0 0 6.6 6.6l2.2-2.2a1 1 0 0 1 1-.25 11.4 11.4 0 0 0 3.6.57 1 1 0 0 1 1 1V20a1 1 0 0 1-1 1A17 17 0 0 1 3 4a1 1 0 0 1 1-1h3.5a1 1 0 0 1 1 1c0 1.25.2 2.45.57 3.57a1 1 0 0 1-.25 1z"/></svg>(432)555-0187</li>
        <li><svg viewBox="0 0 24 24"><path d="M2 5h20v14H2zM4 7v.5l8 5 8-5V7l-8 5z"/></svg>sales@veldmarksupplies.com</li>
        <li><svg viewBox="0 0 24 24"><circle cx="12" cy="12" r="10"/></svg>www.veldmarksupplies.com</li>
      </ul>
    </div>
  </section>
</main>
</body>
</html>
```